NimbaVault Website Homepage Design

Please provide your idea of homepage for a hosting company. This project is for DESIGN only, no coding.

It must use/combine colors used in logo, clean, modern look.

Homepage must consist of at least 4 sections (example: testimonials, services, and so on. not necesarily all of them). We would like the navigation to be horizontal, but not mandatory.

You can include a preview of services page (optional, not a must).

Number of Pages Required

1 page

Font styles to use
Sans Serif

```html
<!DOCTYPE html>
<html lang="en">
<head>
<meta charset="utf-8">
<title>NimbaVault — Hosting</title>
<link href="https://fonts.googleapis.com/css2?family=Poppins:wght@300;400;500;600&family=Rubik:wght@500;600&display=swap" rel="stylesheet">
<style>
:root{
  --blue:#1a6fe0;
  --blue-deep:#0c2fa8;
  --blue-dark:#071b7a;
  --ink:#3a3a3a;
  --text:#555;
  --muted:#777;
  --black:#000;
  --footer:#0a0e1c;
  --white:#fff;
  --line:#e6e6e6;
}
*{margin:0;padding:0;box-sizing:border-box}
html,body{width:1200px;height:3333px;overflow:hidden}
body{position:relative;font-family:"Poppins",sans-serif;color:var(--text);background:var(--white)}
.abs{position:absolute}
a{color:inherit;text-decoration:none}

/* nav */
.topbar{left:0;top:0;width:1200px;height:78px;background:var(--white);box-shadow:0 1px 6px rgba(0,0,0,.08);z-index:2}
.brand{font-family:"Poppins",sans-serif;font-weight:600;font-size:32px;color:var(--blue);letter-spacing:.5px;display:flex;align-items:center;gap:10px}
.brand .dot{width:14px;height:14px;border-radius:50%;background:var(--blue)}
.topbar .brand{left:110px;top:18px}
.menu{right:110px;top:29px;display:flex;gap:37px;font-size:14px;color:#444}
.menu .active{color:var(--blue)}

/* hero */
.hero{left:0;top:78px;width:1200px;height:617px;background:radial-gradient(ellipse at 75% 45%,#1e63e6 0%,#1040c4 45%,#0a2596 100%)}
.hero-welcome{left:112px;top:220px;font-size:38px;color:var(--white);font-weight:400}
.hero-title{left:110px;top:262px;font-size:78px;color:var(--white);font-weight:600;letter-spacing:.5px}
.hero-sub{left:112px;top:358px;font-size:29px;line-height:46px;color:var(--white);font-weight:300}
.hero-art{left:570px;top:120px;width:520px;height:480px;border-radius:50%;background:radial-gradient(circle,#5a8cf5 0%,#2e62e0 45%,rgba(30,80,220,0) 72%)}
.arrow{width:46px;height:46px;border-radius:50%;display:flex;align-items:center;justify-content:center}
.arrow.outline{border:2px solid var(--white)}
.arrow.solid{background:var(--blue)}
.arrow.blue-outline{border:2px solid var(--blue)}

/* section heads */
.kicker{font-size:17px;color:var(--ink);font-weight:400}
.heading{font-family:"Rubik",sans-serif;font-weight:600;font-size:33px;line-height:46px;color:#444;width:460px}
.lead{font-size:14px;line-height:21.5px;color:var(--text);width:480px}

/* services grid */
.grid{left:110px;top:966px;width:981px;height:666px;display:grid;grid-template-columns:repeat(4,245.25px);grid-template-rows:repeat(2,333px);box-shadow:0 2px 14px rgba(0,0,0,.1)}
.tile{background:var(--white);padding:46px 20px 0 20px}
.tile svg{display:block;margin-bottom:12px}
.tile h3{font-size:18px;font-weight:500;color:#444;margin-bottom:12px}
.tile p{font-size:13.5px;line-height:21.5px;color:var(--muted)}
.tile .more{display:inline-block;margin-top:16px;font-size:13px;color:#444;border-bottom:1px solid #444;line-height:18px}
.photo{display:block}
.ph-servers{background:radial-gradient(circle at 50% 60%,#3fa6ff 0%,#1b4ec4 45%,#07154a 100%)}
.ph-cloud{background:radial-gradient(circle at 50% 45%,#6e9bd6 0%,#20406f 50%,#0b1224 100%)}
.ph-browser{background:linear-gradient(160deg,#2c3a73 0%,#b9c7ea 35%,#e8ecf6 100%)}
.ph-hall{background:linear-gradient(180deg,#c8d4e4 0%,#5a6c88 45%,#141c2c 100%)}

/* about */
.about-band{left:0;top:1728px;width:1200px;height:447px;background:var(--black)}
.about-band .kicker,.about-band .heading,.about-band .lead{color:var(--white)}
.video{left:111px;top:2027px;width:978px;height:443px;background:radial-gradient(circle at 68% 40%,#2aa0e8 0%,#0d3a78 35%,#06121f 75%)}
.play{left:546px;top:2196px;width:104px;height:104px;border-radius:50%;border:5px solid var(--white)}

/* testimonials */
.card{top:2724px;width:311px;height:202px;background:var(--white);box-shadow:0 1px 8px rgba(0,0,0,.18);padding:16px 14px}
.card .avatar{position:absolute;left:12px;top:16px;width:64px;height:64px;border-radius:50%;background:linear-gradient(135deg,#c9a080,#6d5443)}
.card .who{position:absolute;left:92px;top:26px}
.card .who b{display:block;font-family:"Rubik",sans-serif;font-weight:500;font-size:18px;color:#333}
.card .who span{font-size:14px;color:#888}
.card p{position:absolute;left:14px;top:98px;width:284px;font-size:13px;line-height:18px;color:#666}

/* newsletter & footer */
.footer{left:0;top:3085px;width:1200px;height:248px;background:var(--footer)}
.news{left:111px;top:3020px;width:975px;height:133px;background:var(--blue);border:3px solid var(--white);border-top:none}
.news h2{position:absolute;left:70px;top:44px;font-size:31px;font-weight:400;color:var(--white)}
.news .field{position:absolute;left:444px;top:45px;width:302px;height:40px;background:var(--white);border-radius:2px;font-size:15px;color:#888;padding:10px 16px}
.news .btn{position:absolute;left:757px;top:45px;width:142px;height:40px;border:1.5px solid var(--white);color:var(--white);font-size:18px;font-weight:500;text-align:center;line-height:37px}
.footer .brand{left:110px;top:112px}
.socials{left:525px;top:130px;display:flex;gap:10px}
.socials span{width:30px;height:30px;border-radius:50%;background:var(--white)}
.help{right:113px;top:118px;text-align:right;color:var(--white)}
.help small{display:block;font-size:13px;font-weight:500}
.help strong{display:block;font-size:26px;font-weight:600;margin-top:4px}
.rule{left:110px;top:183px;width:977px;height:1px;background:#3a3f52}
.foot-links{left:110px;top:205px;display:flex;gap:34px;font-size:13.5px;color:var(--white)}
.copy{right:113px;top:205px;font-size:13.5px;color:var(--white)}
</style>
</head>
<body>

<header class="abs topbar">
  <div class="abs brand"><span class="dot"></span>NimbaVault</div>
  <nav class="abs menu">
    <a class="active">Home</a><a>About us</a><a>Services</a><a>Testimonials</a><a>Blog</a><a>Contact Us</a>
  </nav>
</header>

<section class="abs hero">
  <div class="abs hero-art" role="img" aria-label="Isometric illustration of a server tower with cloud, folders and glowing orbit lines"></div>
  <div class="abs arrow outline" style="left:39px;top:286px">
    <svg width="16" height="16" viewBox="0 0 16 16"><path d="M10 2 4 8l6 6" fill="none" stroke="#fff" stroke-width="2"/></svg>
  </div>
  <div class="abs arrow solid" style="left:1115px;top:286px">
    <svg width="16" height="16" viewBox="0 0 16 16"><path d="M6 2l6 6-6 6" fill="none" stroke="#fff" stroke-width="2"/></svg>
  </div>
  <p class="abs hero-welcome">Welcome to</p>
  <h1 class="abs hero-title">NimbaVault</h1>
  <p class="abs hero-sub">We are a hosting company<br>from Romania</p>
</section>

<section>
  <p class="abs kicker" style="left:108px;top:757px">Services We Offer</p>
  <h2 class="abs heading" style="left:108px;top:787px">Neque porro Quisquam est qui dolorem ipsum quia dolor sit amet.</h2>
  <p class="abs lead" style="left:598px;top:756px">Lorem Ipsum is simply dummy text of the printing and typesetting industry. Lorem Ipsum has been the industry's standard dummy text ever since the 1500s, when an unknown printer took a galley of type and scrambled</p>

  <div class="abs grid">
    <div class="photo ph-servers" role="img" aria-label="Glowing blue server racks"></div>
    <div class="tile">
      <svg width="54" height="54" viewBox="0 0 54 54" fill="none" stroke="#1a6fe0" stroke-width="2.5"><rect x="4" y="24" width="46" height="22" rx="3"/><path d="M14 24V10a13 13 0 0 1 26 0v14"/><path d="M11 35h32M11 40h32"/></svg>
      <h3>Web Hosting</h3>
      <p>Lorem Ipsum is simply dummy text of the printing and typesetting industry. Lorem Ipsum has been the industry's standard dummy text ever</p>
      <a class="more">Read More ›</a>
    </div>
    <div class="photo ph-cloud" role="img" aria-label="Cloud icon over a network of connected devices"></div>
    <div class="tile">
      <svg width="64" height="64" viewBox="0 0 64 64" fill="none" stroke="#1a6fe0" stroke-width="2.5"><path d="M16 30a10 10 0 0 1 4-19 14 14 0 0 1 26 4 8 8 0 0 1 2 15z"/><path d="M32 30v10M12 40h40M12 40v6M32 40v6M52 40v6"/><rect x="5" y="46" width="14" height="12"/><rect x="25" y="46" width="14" height="12"/><rect x="45" y="46" width="14" height="12"/></svg>
      <h3>Cloud Hosting</h3>
      <p>Lorem Ipsum is simply dummy text of the printing and typesetting industry. Lorem Ipsum has been the industry's standard dummy text ever</p>
      <a class="more">Read More ›</a>
    </div>
    <div class="tile">
      <svg width="54" height="54" viewBox="0 0 54 54" fill="none" stroke="#1a6fe0" stroke-width="3"><circle cx="27" cy="27" r="24"/><circle cx="27" cy="27" r="18"/></svg>
      <h3>Blogsite Hosting</h3>
      <p>Lorem Ipsum is simply dummy text of the printing and typesetting industry. Lorem Ipsum has been the industry's standard dummy text ever</p>
      <a class="more">Read More ›</a>
    </div>
    <div class="photo ph-browser" role="img" aria-label="Close-up of a browser window showing a blog sign-in page"></div>
    <div class="tile">
      <svg width="58" height="54" viewBox="0 0 58 54" fill="none" stroke="#1a6fe0" stroke-width="2.5"><rect x="4" y="6" width="30" height="9"/><rect x="4" y="15" width="30" height="9"/><rect x="4" y="24" width="30" height="9"/><rect x="4" y="33" width="30" height="9"/><circle cx="42" cy="36" r="13"/><path d="M46 31h-6a3 3 0 0 0 0 6h4a3 3 0 0 1 0 6h-6M42 28v3M42 43v3"/></svg>
      <h3>Dedicated Server</h3>
      <p>Lorem Ipsum is simply dummy text of the printing and typesetting industry. Lorem Ipsum has been the industry's standard dummy text ever</p>
      <a class="more">Read More ›</a>
    </div>
    <div class="photo ph-hall" role="img" aria-label="Data center corridor lined with server cabinets"></div>
  </div>
</section>

<section>
  <div class="abs about-band">
    <p class="abs kicker" style="left:108px;top:62px">About NimbaVault</p>
    <h2 class="abs heading" style="left:108px;top:92px">Neque porro Quisquam est qui dolorem ipsum quia dolor sit amet.</h2>
    <p class="abs lead" style="left:598px;top:60px">Lorem Ipsum is simply dummy text of the printing and typesetting industry. Lorem Ipsum has been the industry's standard dummy text ever since the 1500s, when an unknown printer took a galley of type and scrambled it to make a type specimen book. It has survived not only five centuries, but also the leap into electronic typesetting, remaining essentially unchanged. It was popularised in the 1960s with the release of Typeset sheets containing Lorem Ipsum passages, and more recently with desktop publishing software like LayoutDesk including versions of Lorem Ipsum.</p>
  </div>
  <div class="abs video" role="img" aria-label="Video still: a hand touching a glowing cloud interface among network icons"></div>
  <div class="abs play">
    <svg class="abs" style="left:30px;top:24px" width="44" height="46" viewBox="0 0 44 46"><path d="M6 4l34 19L6 42z" fill="none" stroke="#fff" stroke-width="5" stroke-linejoin="round"/></svg>
  </div>
</section>

<section>
  <p class="abs kicker" style="left:112px;top:2535px">Testimonials</p>
  <h2 class="abs heading" style="left:112px;top:2565px">Neque porro Quisquam est qui dolorem ipsum quia dolor sit amet.</h2>
  <div class="abs arrow blue-outline" style="left:39px;top:2802px">
    <svg width="16" height="16" viewBox="0 0 16 16"><path d="M10 2 4 8l6 6" fill="none" stroke="#1a6fe0" stroke-width="2"/></svg>
  </div>
  <div class="abs arrow solid" style="left:1115px;top:2802px">
    <svg width="16" height="16" viewBox="0 0 16 16"><path d="M6 2l6 6-6 6" fill="none" stroke="#fff" stroke-width="2"/></svg>
  </div>
  <div class="abs card" style="left:115px">
    <div class="avatar" role="img" aria-label="Customer portrait"></div>
    <div class="who"><b>Mara L Quinn</b><span>female</span></div>
    <p>Lorem Ipsum is simply dummy text of the printing and typesetting industry. Lorem Ipsum has been the industry's standard dummy text ever since the 1500s, when an unknown printer took...</p>
  </div>
  <div class="abs card" style="left:445px">
    <div class="avatar" role="img" aria-label="Customer portrait"></div>
    <div class="who"><b>Mara L Quinn</b><span>female</span></div>
    <p>Lorem Ipsum is simply dummy text of the printing and typesetting industry. Lorem Ipsum has been the industry's standard dummy text ever since the 1500s, when an unknown printer took...</p>
  </div>
  <div class="abs card" style="left:776px">
    <div class="avatar" role="img" aria-label="Customer portrait"></div>
    <div class="who"><b>Mara L Quinn</b><span>female</span></div>
    <p>Lorem Ipsum is simply dummy text of the printing and typesetting industry. Lorem Ipsum has been the industry's standard dummy text ever since the 1500s, when an unknown printer took...</p>
  </div>
</section>

<footer class="abs footer">
  <div class="abs brand"><span class="dot"></span>NimbaVault</div>
  <div class="abs socials"><span></span><span></span><span></span><span></span></div>
  <div class="abs help"><small>Need Help?</small><strong>+310-555-0148</strong></div>
  <div class="abs rule"></div>
  <nav class="abs foot-links"><a>Home</a><a>About us</a><a>Services</a><a>Testimonials</a><a>Blog</a><a>Contact Us</a></nav>
  <p class="abs copy">NimbaVault. &nbsp;© 2021.All Rights Reserved.</p>
</footer>

<div class="abs news">
  <h2>Sign up for newsletter</h2>
  <div class="field">Your Email</div>
  <div class="btn">SIGN UP</div>
</div>

</body>
</html>
```